Plakate für Haushaltshilfen und Alltagsbegleiter
Zielgruppe
Wir bieten haushaltsnahe Dienstleistungen (Haushaltshilfen und Altgasbegleiter) für Personen mit einem Pflegegrad 1 - 5 an.
Zielgruppe sind Personen mit einem Pflegegrad 1 - 5. Hauptsächlich ältere Menschen die Unterstützung/Betreuung im Alltag und Haushalt benötigen.
Aufgabenstellung
Wir benötigen für unsere Büroräume eine Fensterbeschriftung. Es handelt sich hier um 5 Fenster (Glasflächen) und eine Glastür. Die Vorgabe ist, dass von außen zu erkennen ist dass sich um alle Räumlichkeiten um unsere (Firma Lindwerk) Räumlichkeiten handelt. Desweiteren soll auch unser Angebot erkennbar sein.
Unser Angebot enthält: Haushaltshilfen und Alltagsbegleiter
- kostenlose Haushaltshilfe ab Pflegegrad 1
- Abrechnung mit allen Kostenträgern
Da wir keine Schilder an die Fassade anbringen können, müßen die Glasflächen dafür genutzt werden um zum Einen uns als Firma erkennbar zu machen und zum anderen unser Angebot kurz zu präsentieren.
Uns ist wichtig dass unser Logo verwendet wir und auch unsere Farben.
Desweiteren sollten an den Fenstern auch teilweise eine Sichtschutz nach innen, angebracht werden, aber eben nur teilweise also nicht das ganzen Fenster z.Bsp. mit einer Blickdichten Folie überziehen, sondern in Augenhöhe wenn Fußgänger vorbei laufen.

```html
<!DOCTYPE html>
<html lang="de">
<head>
<meta charset="utf-8">
<title>Lindwerk – Fensterbeschriftung</title>
<link rel="stylesheet" href="https://fonts.googleapis.com/css2?family=Cinzel:wght@600;700&family=Poppins:wght@400;600;700&family=Kalam:wght@700&display=swap">
<style>
  :root{
    --red:#c8202f;
    --ink:#2e2e2e;
    --dark:#2f2f31;
    --white:#ffffff;
    --frame:#9d9d9f;
    --backdrop:#c6c6c7;
    --mist:#e6e8ea;
  }
  *{margin:0;padding:0;box-sizing:border-box}
  html,body{width:1200px;height:2235px;overflow:hidden;background:var(--backdrop)}
  .canvas{position:relative;width:1200px;height:2235px}
  .window-frame{position:absolute;background:var(--frame)}
  .poster{position:absolute;overflow:hidden;background:var(--white)}
  .poster svg.shapes{position:absolute;left:0;top:0;width:100%;height:100%}
  .txt{position:absolute;left:0;width:100%;text-align:center}
  .brand{font-family:"Cinzel",serif;font-weight:700;color:var(--ink);letter-spacing:1px}
  .tagline{font-family:"Cinzel",serif;font-weight:700;color:var(--red);letter-spacing:.5px}
  .headline{font-family:"Cinzel",serif;font-weight:700;line-height:1.12}
  .headline .accent{color:var(--red)}
  .headline .plain{color:var(--ink)}
  .sans{font-family:"Poppins",sans-serif}
  .script{font-family:"Kalam",cursive;color:var(--red);font-weight:700;transform:rotate(-8deg)}
  .phone-line{display:flex;align-items:center;justify-content:center;gap:6px;font-family:"Poppins",sans-serif;font-weight:700}
  .logo-dot{position:absolute;border-radius:50%;border:5px solid var(--red)}
  .brand-row{position:absolute;display:flex;align-items:center;gap:8px}
  .brand-row .mark{width:30px;height:30px;border-radius:50%;border:3px solid var(--white)}
  .brand-row .name{font-family:"Cinzel",serif;font-weight:700;color:var(--white);font-size:22px;line-height:1}
  .brand-row .sub{font-family:"Cinzel",serif;font-weight:700;color:var(--white);font-size:7px;letter-spacing:.5px}
</style>
</head>
<body>
<div class="canvas">

  <!-- upper row: three window panels -->
  <div class="window-frame" style="left:63px;top:470px;width:1074px;height:488px"></div>

  <!-- panel 1 -->
  <div class="poster" style="left:85px;top:490px;width:329px;height:447px">
    <svg class="shapes" viewBox="0 0 329 447" preserveAspectRatio="none">
      <rect width="329" height="447" fill="var(--white)"/>
      <rect y="210" width="329" height="110" fill="var(--mist)"/>
      <path d="M0 150 C70 175 150 205 329 200 L329 214 C150 225 60 218 0 215 Z" fill="var(--dark)"/>
      <path d="M0 325 C110 300 220 300 329 322 L329 345 C220 322 110 322 0 348 Z" fill="var(--red)"/>
      <path d="M0 348 C110 322 220 322 329 345 L329 447 L0 447 Z" fill="var(--dark)"/>
    </svg>
    <div class="txt brand" style="top:14px;font-size:36px">LINDWERK</div>
    <div class="txt tagline" style="top:56px;font-size:12.5px">HAUSHALTSHILFEN &amp; MEHR</div>
    <div class="logo-dot" style="left:109px;top:85px;width:112px;height:112px"></div>
    <div class="txt headline" style="top:258px;font-size:17px"><span class="accent">HAUSHALTSHILFEN &amp;</span><br><span class="plain">ALLTAGSBEGLEITER</span></div>
    <div class="txt sans" style="top:368px;font-size:8.5px;color:var(--white)">Buchen Sie gleich einen Termin:</div>
    <div class="txt phone-line" style="top:382px;font-size:24px;color:var(--white)">
      <svg width="20" height="20" viewBox="0 0 20 20"><circle cx="10" cy="10" r="10" fill="var(--red)"/><path d="M6.5 5 L8.5 5 L9.3 7.6 L8 8.6 C8.6 10 9.9 11.3 11.4 12 L12.4 10.7 L15 11.5 L15 13.5 C11 14.5 5.5 9 6.5 5 Z" fill="var(--white)"/></svg>0711 98 76 54 32</div>
    <div class="txt sans" style="top:420px;font-size:9.5px;letter-spacing:2px;font-weight:600;color:var(--white)">www.lindwerk-hilfe.de</div>
  </div>

  <!-- panel 2 -->
  <div class="poster" style="left:435px;top:490px;width:329px;height:447px">
    <svg class="shapes" viewBox="0 0 329 447" preserveAspectRatio="none">
      <rect width="329" height="447" fill="var(--white)"/>
      <rect y="210" width="329" height="110" fill="var(--mist)"/>
      <path d="M0 150 C70 175 150 205 329 200 L329 214 C150 225 60 218 0 215 Z" fill="var(--dark)"/>
      <path d="M0 325 C110 300 220 300 329 322 L329 345 C220 322 110 322 0 348 Z" fill="var(--red)"/>
      <path d="M0 348 C110 322 220 322 329 345 L329 447 L0 447 Z" fill="var(--dark)"/>
    </svg>
    <div class="txt brand" style="top:14px;font-size:36px">LINDWERK</div>
    <div class="txt tagline" style="top:56px;font-size:12.5px">HAUSHALTSHILFEN &amp; MEHR</div>
    <div class="logo-dot" style="left:109px;top:85px;width:112px;height:112px"></div>
    <div class="txt headline" style="top:240px;font-size:17px"><span class="accent">KOSTENLOSE<br>HAUSHALTSHILFE AB</span><br><span class="plain">PFLEGEGRAD 1</span></div>
    <div class="txt sans" style="top:368px;font-size:8.5px;color:var(--white)">Buchen Sie gleich einen Termin:</div>
    <div class="txt phone-line" style="top:382px;font-size:24px;color:var(--white)">
      <svg width="20" height="20" viewBox="0 0 20 20"><circle cx="10" cy="10" r="10" fill="var(--red)"/><path d="M6.5 5 L8.5 5 L9.3 7.6 L8 8.6 C8.6 10 9.9 11.3 11.4 12 L12.4 10.7 L15 11.5 L15 13.5 C11 14.5 5.5 9 6.5 5 Z" fill="var(--white)"/></svg>0711 98 76 54 32</div>
    <div class="txt sans" style="top:420px;font-size:9.5px;letter-spacing:2px;font-weight:600;color:var(--white)">www.lindwerk-hilfe.de</div>
  </div>

  <!-- panel 3 -->
  <div class="poster" style="left:785px;top:490px;width:329px;height:447px">
    <svg class="shapes" viewBox="0 0 329 447" preserveAspectRatio="none">
      <rect width="329" height="447" fill="var(--white)"/>
      <rect y="210" width="329" height="110" fill="var(--mist)"/>
      <path d="M0 150 C70 175 150 205 329 200 L329 214 C150 225 60 218 0 215 Z" fill="var(--dark)"/>
      <path d="M0 325 C110 300 220 300 329 322 L329 345 C220 322 110 322 0 348 Z" fill="var(--red)"/>
      <path d="M0 348 C110 322 220 322 329 345 L329 447 L0 447 Z" fill="var(--dark)"/>
    </svg>
    <div class="txt brand" style="top:14px;font-size:36px">LINDWERK</div>
    <div class="txt tagline" style="top:56px;font-size:12.5px">HAUSHALTSHILFEN &amp; MEHR</div>
    <div class="logo-dot" style="left:109px;top:85px;width:112px;height:112px"></div>
    <div class="txt headline" style="top:258px;font-size:17px"><span class="accent">ABRECHNUNG MIT</span><br><span class="plain">ALLEN KOSTENTRÄGERN</span></div>
    <div class="txt sans" style="top:368px;font-size:8.5px;color:var(--white)">Buchen Sie gleich einen Termin:</div>
    <div class="txt phone-line" style="top:382px;font-size:24px;color:var(--white)">
      <svg width="20" height="20" viewBox="0 0 20 20"><circle cx="10" cy="10" r="10" fill="var(--red)"/><path d="M6.5 5 L8.5 5 L9.3 7.6 L8 8.6 C8.6 10 9.9 11.3 11.4 12 L12.4 10.7 L15 11.5 L15 13.5 C11 14.5 5.5 9 6.5 5 Z" fill="var(--white)"/></svg>0711 98 76 54 32</div>
    <div class="txt sans" style="top:420px;font-size:9.5px;letter-spacing:2px;font-weight:600;color:var(--white)">www.lindwerk-hilfe.de</div>
  </div>

  <!-- lower row: two windows and the glass door -->
  <div class="window-frame" style="left:63px;top:989px;width:350px;height:569px"></div>
  <div class="window-frame" style="left:764px;top:989px;width:373px;height:569px"></div>
  <div class="window-frame" style="left:413px;top:989px;width:351px;height:774px"></div>

  <!-- lower left window -->
  <div class="poster" style="left:85px;top:1009px;width:329px;height:529px;background:var(--dark)">
    <svg class="shapes" viewBox="0 0 329 529" preserveAspectRatio="none">
      <rect width="329" height="529" fill="var(--dark)"/>
      <path d="M329 20 C250 60 270 110 170 110 C70 110 20 170 20 260 C20 360 100 420 200 420 C280 420 329 380 329 380 Z" fill="var(--white)"/>
      <path d="M329 0 L329 20 C250 60 270 110 170 110 C230 90 260 40 300 0 Z" fill="var(--red)"/>
      <path d="M0 400 C60 440 220 450 329 400 L329 425 C220 475 60 465 0 430 Z" fill="var(--red)"/>
      <path d="M0 370 C50 420 200 440 329 380 L329 400 C220 450 60 440 0 400 Z" fill="var(--white)"/>
    </svg>
    <div class="brand-row" style="left:22px;top:26px"><div class="mark"></div><div><div class="name">LINDWERK</div><div class="sub">HAUSHALTSHILFEN &amp; MEHR</div></div></div>
    <div class="script" style="position:absolute;left:212px;top:105px;font-size:20px;line-height:.95;text-align:center">Wir Sind<br>für Sie da!</div>
    <div class="txt headline" style="top:180px;font-size:15px;color:var(--red);letter-spacing:.5px">BIETEN WIR IHNEN<br>BEDARFSORIENTIERTE<br>HILFE RUND UM<br>DEN HAUSHALT AN.</div>
    <div class="txt sans" style="top:262px;left:40px;width:250px;font-size:9px;color:#6b6b6b;line-height:1.35">Mit unserem breiten Spektrum an Services möchten wir Sie beim bewältigen des Alltags unterstützen.</div>
    <div class="logo-dot" style="left:133px;top:320px;width:64px;height:64px;border-width:4px"></div>
  </div>

  <!-- glass door -->
  <div style="position:absolute;left:435px;top:1009px;width:329px;height:731px;background:var(--dark)"></div>
  <div class="poster" style="left:435px;top:1158px;width:329px;height:430px">
    <svg class="shapes" viewBox="0 0 329 430" preserveAspectRatio="none">
      <rect width="329" height="430" fill="var(--white)"/>
      <path d="M0 340 C80 400 250 400 329 330 L329 352 C250 420 80 420 0 362 Z" fill="var(--red)"/>
      <path d="M0 362 C80 420 250 420 329 352 L329 368 C250 435 80 435 0 378 Z" fill="var(--dark)"/>
    </svg>
    <div class="logo-dot" style="left:114px;top:30px;width:100px;height:100px"></div>
    <div class="txt brand" style="top:165px;font-size:38px">LINDWERK</div>
    <div class="txt tagline" style="top:210px;font-size:13px">HAUSHALTSHILFEN &amp; MEHR</div>
    <div class="txt sans" style="top:236px;font-size:8.5px;color:var(--red);font-weight:600">Buchen Sie gleich einen Termin:</div>
    <div style="position:absolute;left:54px;top:250px;width:221px;height:34px;border:2px solid var(--red);border-radius:17px"></div>
    <div class="txt phone-line" style="top:254px;font-size:21px;color:var(--ink)">
      <svg width="20" height="20" viewBox="0 0 20 20"><circle cx="10" cy="10" r="10" fill="var(--red)"/><path d="M6.5 5 L8.5 5 L9.3 7.6 L8 8.6 C8.6 10 9.9 11.3 11.4 12 L12.4 10.7 L15 11.5 L15 13.5 C11 14.5 5.5 9 6.5 5 Z" fill="var(--white)"/></svg>0711 98 76 54 32</div>
    <div class="txt sans" style="top:294px;font-size:10px;color:var(--ink);line-height:1.4">
      <svg width="9" height="12" viewBox="0 0 9 12" style="vertical-align:-1px"><path d="M4.5 0 C7 0 9 2 9 4.5 C9 7.5 4.5 12 4.5 12 C4.5 12 0 7.5 0 4.5 C0 2 2 0 4.5 0 Z" fill="var(--red)"/><circle cx="4.5" cy="4.5" r="1.7" fill="var(--white)"/></svg>
      Firma Lindwerk, Renate Vogler<br>Lindenweg 14,<br>70599 Stuttgart</div>
  </div>

  <!-- lower right window -->
  <div class="poster" style="left:785px;top:1009px;width:329px;height:529px;background:var(--dark)">
    <svg class="shapes" viewBox="0 0 329 529" preserveAspectRatio="none">
      <rect width="329" height="529" fill="var(--dark)"/>
      <path d="M329 20 C250 60 270 110 170 110 C70 110 10 170 10 260 C10 360 100 420 200 420 C280 420 329 380 329 380 Z" fill="var(--white)"/>
      <path d="M329 0 L329 20 C250 60 270 110 170 110 C230 90 260 40 300 0 Z" fill="var(--red)"/>
      <path d="M0 400 C60 440 220 450 329 400 L329 425 C220 475 60 465 0 430 Z" fill="var(--red)"/>
      <path d="M0 370 C50 420 200 440 329 380 L329 400 C220 450 60 440 0 400 Z" fill="var(--white)"/>
    </svg>
    <div class="brand-row" style="left:22px;top:26px"><div class="mark"></div><div><div class="name">LINDWERK</div><div class="sub">HAUSHALTSHILFEN &amp; MEHR</div></div></div>
    <div class="script" style="position:absolute;left:212px;top:105px;font-size:20px;line-height:.95;text-align:center">Wir Sind<br>für Sie da!</div>
    <div class="txt headline" style="top:172px;font-size:17px;color:var(--red)">BENÖTIGEN HILFE<br>IM HAUSHALT?</div>
    <div class="txt headline" style="top:216px;font-size:10px;color:var(--ink)">JETZT KOSTENLOS BERATEN<br>LASSEN!</div>
    <div class="txt headline" style="top:260px;font-size:8px;color:var(--red)">FESTNETZ:</div>
    <div class="txt phone-line" style="top:270px;font-size:19px;color:var(--ink)">
      <svg width="17" height="17" viewBox="0 0 20 20"><circle cx="10" cy="10" r="10" fill="var(--red)"/><path d="M6.5 5 L8.5 5 L9.3 7.6 L8 8.6 C8.6 10 9.9 11.3 11.4 12 L12.4 10.7 L15 11.5 L15 13.5 C11 14.5 5.5 9 6.5 5 Z" fill="var(--white)"/></svg>0711 98 76 54 32</div>
    <div class="txt headline" style="top:298px;font-size:8px;color:var(--red)">24/7 MOBIL:</div>
    <div class="txt phone-line" style="top:308px;font-size:19px;color:var(--ink)">
      <svg width="17" height="17" viewBox="0 0 20 20"><circle cx="10" cy="10" r="10" fill="var(--red)"/><path d="M6.5 5 L8.5 5 L9.3 7.6 L8 8.6 C8.6 10 9.9 11.3 11.4 12 L12.4 10.7 L15 11.5 L15 13.5 C11 14.5 5.5 9 6.5 5 Z" fill="var(--white)"/></svg>0711 98 76 54 32</div>
    <div class="txt sans" style="top:344px;font-size:12px;font-weight:700;color:var(--red)">www.lindwerk-hilfe.de</div>
  </div>

</div>
</body>
</html>
```